NexaBRIDGE new era @ Hyper Digitalization

We need a Brochure that show all our product, services and consulting related to Hyper Digitalization into the industrial internet of things world.
We need a document that can be handled as a electronic brochure, this means that we need to show strong corporate presence, with strong skill of technology, and we have credentials and key sucess projects related to Manufacturing industries.
Key industries that we attend: Automotive, Chemical, Food and Beverage, Mining, Paper and Pulp, Oil and Gas, Energy Management.
We save money to our customer in 6 ways: 1) Eficiency in operation 2) Production Control 3) Hyper Digitalization of Thing Optimizing asset ussage 4) Maintenance and predictive of assets risks 5) Quality Control reducing Cost 6) Augmented Reality in operation and control
Target Market(s)
Manufacturing Industry. CEO of companies that has challenges of saving operation costs into plants of manufacturing.
Industry/Entity Type
Software
Other font styles liked:
- MONTSERRAT
Requirements
Must have
- Technology Enviroment, our logo, our expertise, simple message about what our company does and the DNA, infography of the company, cases of sucess, cases of savings $ using our tecnology and services, what we can do for the customer in a few words
Nice to have
- standarize our colors related to our presentation, futuristic, information related to Artificial Inteligence related to machinery
Should not have
- old version of technology,

```html
<!DOCTYPE html>
<html lang="en">
<head>
<meta charset="utf-8">
<title>NexaBRIDGE Brochure Front</title>
<link href="https://fonts.googleapis.com/css2?family=Montserrat:wght@400;500;700;800&display=swap" rel="stylesheet">
<style>
  :root {
    --stage: #e6e6e6;
    --paper: #ffffff;
    --navy: #1c3b6c;
    --navy-deep: #16305a;
    --teal: #1d8fb3;
    --teal-light: #39b6d3;
    --strip: #4db3d4;
    --ink-grey: #7a7a7a;
    --brand-blue: #1f5fa8;
  }
  * { margin: 0; padding: 0; box-sizing: border-box; }
  html, body {
    width: 993px; height: 1200px; overflow: hidden;
    background: var(--stage);
    font-family: "Montserrat", Arial, sans-serif;
  }
  .brochure {
    position: absolute; left: 72px; top: 0;
    width: 849px; height: 1200px;
    background: var(--paper);
    overflow: hidden;
  }
  .hero-band {
    position: absolute; left: 0; top: 206px;
    width: 849px; height: 742px;
    background: var(--navy);
  }
  .globe-visual {
    position: absolute; left: 280px; top: 206px;
    width: 569px; height: 742px;
    background:
      radial-gradient(ellipse 70% 55% at 75% 58%, rgba(57,182,211,0.85) 0%, rgba(29,143,179,0.6) 40%, rgba(28,59,108,0) 75%),
      radial-gradient(ellipse 60% 35% at 70% 25%, rgba(57,182,211,0.25) 0%, rgba(28,59,108,0) 70%),
      var(--navy);
  }
  .accent-strip {
    position: absolute; left: 0; top: 948px;
    width: 849px; height: 51px;
    background: var(--strip);
  }
  .photo-column { position: absolute; left: 49px; top: 0; width: 231px; }
  .photo-frame {
    position: absolute; left: 0; width: 231px; height: 230px;
    background: var(--paper);
    padding: 5px;
  }
  .photo-frame .photo { width: 100%; height: 100%; }
  .frame-ai { top: 106px; }
  .frame-engineer { top: 357px; }
  .frame-robotics { top: 613px; }
  .frame-analytics { top: 868px; }
  .photo-ai { background: linear-gradient(135deg, #0d2a55 0%, #1d6fb0 55%, #0b1f40 100%); }
  .photo-engineer { background: linear-gradient(135deg, #7a4a3a 0%, #6f7a88 45%, #3c4a63 100%); }
  .photo-robotics { background: linear-gradient(160deg, #c9ced6 0%, #e2dcd2 45%, #5a6374 100%); }
  .photo-analytics { background: linear-gradient(135deg, #c6d6e6 0%, #9fb6cf 50%, #3a4250 100%); }
  .headline {
    position: absolute; right: 51px; top: 692px;
    color: #ffffff;
    font-weight: 700;
    font-size: 37px;
    line-height: 35px;
    letter-spacing: -0.5px;
    text-align: right;
  }
  .website {
    position: absolute; left: 52px; top: 1113px;
    font-size: 16.5px; font-weight: 400;
    color: var(--ink-grey);
    letter-spacing: 0.3px;
  }
  .brand-name {
    position: absolute; right: 51px; top: 1097px;
    font-size: 30px; font-weight: 500;
    color: var(--brand-blue);
    letter-spacing: 0.5px;
  }
</style>
</head>
<body>
  <main class="brochure">
    <div class="hero-band"></div>
    <div class="globe-visual" role="img" aria-label="Glowing globe wrapped in connected network lines and light nodes"></div>
    <div class="accent-strip"></div>

    <div class="photo-column">
      <div class="photo-frame frame-ai"><div class="photo photo-ai" role="img" aria-label="Hands typing on a laptop with a robotic hand and holographic data dashboards"></div></div>
      <div class="photo-frame frame-engineer"><div class="photo photo-engineer" role="img" aria-label="Engineer in a hard hat holding a tablet inside an industrial plant"></div></div>
      <div class="photo-frame frame-robotics"><div class="photo photo-robotics" role="img" aria-label="Industrial robot arms in a factory controlled from a tablet"></div></div>
      <div class="photo-frame frame-analytics"><div class="photo photo-analytics" role="img" aria-label="Businessman drawing on a transparent analytics chart screen"></div></div>
    </div>

    <h1 class="headline">Connecting<br>machines,<br>users and data.</h1>

    <p class="website">www.nexabridge-mx.com</p>
    <p class="brand-name">NexaBRIDGE</p>
  </main>
</body>
</html>
```